Consulting company business cards

We have a base design, but would be willing to update. We have a new logo/"tag" that needs to be added. Current business card design is attached for reference into our "style."

Industry/Entity Type

Business

Contact Information for Business Card

Should contain name and title, office number, mobile number if appropriate, e-mail, website, physical address, and company logo.

Font styles to use
Other font styles liked:
• See current card design on KorvandBCard

Colors
0455a3
85acd3
aaaaaa

Requirements
Must have
• Our colors are navy blue, gray, and a lighter blue
Nice to have
• Design that I can easily drop in new names/titles as we hire employees.

```html
<!DOCTYPE html>
<html lang="en">
<head>
<meta charset="utf-8">
<title>Harlow Business Cards</title>
<link href="https://fonts.googleapis.com/css2?family=Montserrat:wght@400;500;700;800&display=swap" rel="stylesheet">
<style>
  :root {
    --navy: #003356;
    --sky: #3aa8e4;
    --mist: #85acd3;
    --grey: #aaaaaa;
    --paper: #ffffff;
    --backdrop: #e6e8eb;
  }
  * { box-sizing: border-box; margin: 0; padding: 0; }
  html, body { width: 1200px; height: 900px; overflow: hidden; }
  body {
    background: var(--backdrop);
    font-family: "Montserrat", sans-serif;
    display: flex;
    flex-direction: column;
    align-items: center;
    justify-content: center;
    gap: 40px;
  }
  .card {
    width: 700px;
    height: 400px;
    border-radius: 26px;
    background: var(--paper);
    position: relative;
    overflow: hidden;
    box-shadow: 0 8px 24px rgba(0,0,0,.12);
  }

  /* Front */
  .front-mark {
    position: absolute;
    left: 0; right: 0; top: 110px;
    display: flex;
    justify-content: center;
    align-items: center;
    gap: 16px;
  }
  .front-mark .dot {
    width: 46px; height: 46px; border-radius: 50%;
    background: var(--navy);
  }
  .front-mark .name {
    font-weight: 800;
    font-size: 64px;
    letter-spacing: 2px;
    color: var(--navy);
  }
  .front-web {
    position: absolute;
    left: 0; right: 0; bottom: 44px;
    text-align: center;
    font-size: 22px;
    font-weight: 500;
    color: var(--sky);
    letter-spacing: .5px;
  }
  .front-web b { color: var(--navy); font-weight: 700; }

  /* Back */
  .back-logo {
    position: absolute;
    left: 34px; top: 214px;
    display: flex;
    align-items: center;
    gap: 10px;
  }
  .back-logo .name {
    font-weight: 800;
    font-size: 40px;
    letter-spacing: .5px;
    color: var(--navy);
    line-height: 1;
  }
  .back-logo .dot {
    width: 30px; height: 30px; border-radius: 50%;
    background: var(--mist);
  }
  .panel-edge {
    position: absolute;
    left: 292px; top: 0; bottom: 0;
    width: 3px;
    background: var(--sky);
  }
  .panel {
    position: absolute;
    left: 302px; top: 0; right: 0; bottom: 0;
    background: var(--navy);
    color: var(--paper);
    padding: 58px 30px 0 46px;
  }
  .panel-notch {
    position: absolute;
    left: 290px; top: 78px;
    width: 0; height: 0;
    border-top: 12px solid transparent;
    border-bottom: 12px solid transparent;
    border-right: 14px solid var(--navy);
  }
  .person-name {
    font-weight: 700;
    font-size: 27px;
    color: var(--sky);
    letter-spacing: 1px;
  }
  .person-title {
    font-size: 17px;
    font-weight: 500;
    letter-spacing: 1px;
    margin-top: 2px;
  }
  .address {
    font-size: 16px;
    line-height: 1.3;
    margin: 22px 0 0 22px;
  }
  .contact-list {
    list-style: none;
    margin-top: 18px;
    font-size: 16px;
    line-height: 1.45;
  }
  .contact-list li { display: flex; align-items: center; gap: 10px; }
  .contact-list svg { width: 13px; height: 13px; fill: var(--sky); flex: none; }
  .contact-list .web b { color: var(--sky); font-weight: 700; }
</style>
</head>
<body>

<section class="card card-front">
  <div class="front-mark">
    <span class="dot"></span>
    <span class="name">HARLOW</span>
  </div>
  <p class="front-web">www.<b>HARLOWTECH</b>.com</p>
</section>

<section class="card card-back">
  <div class="back-logo">
    <span class="name">HARLOW</span>
    <span class="dot"></span>
  </div>
  <div class="panel-edge"></div>
  <div class="panel-notch"></div>
  <div class="panel">
    <h1 class="person-name">RENATA KORVAND</h1>
    <p class="person-title">OFFICE MANAGER</p>
    <p class="address">1187 w 48th st<br>brookfield indiana 46311</p>
    <ul class="contact-list">
      <li><svg viewBox="0 0 16 16"><path d="M3 1l3 3-2 2c1 2 3 4 5 5l2-2 3 3-2 3C6 15 1 10 1 3z"/></svg><span>555 214 3380</span></li>
      <li><svg viewBox="0 0 16 16"><rect x="4" y="1" width="8" height="14" rx="2"/></svg><span>555 214 3391</span></li>
      <li><svg viewBox="0 0 16 16"><path d="M1 3h14v10H1z M1 3l7 6 7-6" fill="none" stroke="#3aa8e4" stroke-width="1.6"/></svg><span>rkorvand@harlowtech.com</span></li>
      <li class="web"><svg viewBox="0 0 16 16"><circle cx="8" cy="8" r="6.5" fill="none" stroke="#3aa8e4" stroke-width="1.6"/><path d="M1.5 8h13M8 1.5v13" stroke="#3aa8e4" stroke-width="1.2"/></svg><span>www.<b>HARLOWTECH</b>.com</span></li>
    </ul>
  </div>
</section>

</body>
</html>
```